New Design for our Velostine Gran Reserva Brandy, it is the label design for the bottle label

We need a new bottle label for our Brandy Gran Reserva that we want to bring to the market.

Please have a look at all our current bottles and labels and the feel of our company under www.velostine-example.ch

The bottle that we will be using for the brand is a different one than the one that we already have, the design of the bottle is attached with a document.

I have also attached a briefing in regards to Brandy in general for your information.

### 1. What is Brandy?
Brandy is a distilled spirit made from fermented wine or other fruit wines. It is traditionally aged in oak barrels, which gives it its characteristic color and rich flavor. The aging process in oak is essential for developing the aromas and quality of the brandy.

### 2. What is Brandy Reserva?
A Brandy labeled as "Reserva" has undergone a longer aging process, typically at least 2 to 3 years, in oak barrels. This aging gives the brandy a deeper, more complex flavor profile and a darker color. "Reserva" is often an indication of higher quality.

### 3. Who enjoys drinking Brandy?
Brandy is typically favored by those who appreciate a deep, rich tasting experience. This often includes older consumers who value the time-aged complexity of the spirit. However, Brandy is also gaining popularity among younger people, especially through cocktails and modern serving styles.

### 4. Why is Brandy trending?
Brandy is experiencing a resurgence as consumers increasingly value quality and artisanal production methods. Its versatility in cocktails and association with traditional, luxurious experiences have also contributed to its renewed popularity.

### 5. What colors would be associated with Brandy?
The typical colors associated with Brandy are warm gold, amber, and deep golden-brown tones. These colors reflect the aging process in oak barrels and the richness of the flavors. Other associated colors might include dark brown and mahogany.

### 6. What is important to customers when buying Brandy?
Customers care about the origin of the Brandy, the aging time, the quality of the ingredients, the production method, and the brand. They also pay attention to the prestige of the product and the authenticity of the production.

### 7. What is not important to customers when buying Brandy?
For many customers, the price and packaging (unless it’s especially exclusive) may be less important than the quality and taste of the Brandy. The distillery name might be less significant if it isn’t tied to a particular reputation.

### 8. What do customers know about Swiss Brandy?
Swiss Brandy is still relatively unknown in many markets, but customers who are familiar with it appreciate the precision and quality of Swiss production. Swiss Brandy is assumed to be made with care and under strict quality standards.

### 9. What is Brandy Gran Reserva?
**Brandy Gran Reserva** is an even higher quality and longer-aged version of Brandy. Generally, a Gran Reserva is aged for at least 5 to 10 years or more in oak barrels. This extended aging process gives the Brandy an especially deep, complex flavor profile and often a darker, richer color. Gran Reserva is often regarded as the top-tier product within a Brandy range and appeals to discerning consumers who value quality, refinement, and a luxurious tasting experience.

The label “Gran Reserva” thus indicates the highest quality level for Brandies, similar to other spirits (like wine or whisky), where the aging time is a critical factor.

### 10. What emotions are associated with Brandy?
Brandy is often associated with luxury, relaxation, and comfort. It evokes feelings of tradition, elegance, and sophistication. Drinking Brandy is frequently seen as a moment of reflection and enjoyment.

### 11. How should Brandy be marketed?
Brandy should be marketed with a focus on its artisanal production, quality, and tradition. A narrative around the product, its aging, and origin can help create an emotional connection with the customer. The marketing should also emphasize the versatility of Brandy, whether consumed neat or in cocktails.

### 12. Sales test and label design for Velostine Brandy
For a sales test, I would suggest a tasting in an upscale setting, perhaps paired with a storytelling presentation highlighting the history of the 6-year aged Brandy and its aging in oak barrels.

**Label design**:
The label should reflect the exclusivity of the product, with an elegant, minimalist design. Colors like deep gold, mahogany, and a hint of deep blue could be used to emphasize the aging and quality of the Brandy. The label should include information about the aging time, the use of oak barrels, and a brief story about the Brandy’s production. A seal or embossing highlighting the craftsmanship would also be fitting.

Target Market(s)

Customers that like Brandy

Requirements
Must have
• the Alcohol % must be included on the label as well as our address.

```html
<!DOCTYPE html>
<html lang="en">
<head>
<meta charset="utf-8">
<title>Velostine Gran Reserva Brandy – Label Set</title>
<link rel="stylesheet" href="https://fonts.googleapis.com/css2?family=Cinzel:wght@400;600;700&family=Cormorant+Garamond:ital,wght@0,500;1,400;1,500&family=Great+Vibes&display=swap">
<style>
  :root {
    --bg: #ffffff;
    --navy: #14223d;
    --ink-black: #15120e;
    --gold: #b08a4a;
    --gold-light: #cfae72;
    --gold-dark: #8a6a35;
    --paper: #f1ede2;
    --paper-ink: #6b5a44;
    --silver: #d9dde3;
    --swiss-red: #d52b1e;
    --wax: #a3141b;
    --white: #ffffff;
  }
  * { margin: 0; padding: 0; box-sizing: border-box; }
  html, body { width: 1200px; height: 1200px; overflow: hidden; background: var(--bg); }
  .canvas { position: relative; width: 1200px; height: 1200px; }

  /* Neck label */
  .neck-label {
    position: absolute; left: 549px; top: 60px; width: 102px; height: 424px;
    border-radius: 4px; overflow: hidden; background: var(--paper);
  }
  .neck-label__band {
    height: 304px; background: var(--ink-black);
    display: flex; align-items: center; justify-content: center;
  }
  .neck-label__title {
    transform: rotate(-90deg); white-space: nowrap;
    font-family: 'Cinzel', serif; font-weight: 600; font-size: 30px; color: var(--gold);
    letter-spacing: 1px;
  }
  .neck-label__foot { text-align: center; padding-top: 22px; }
  .neck-label__sub {
    font-family: 'Cinzel', serif; font-size: 10px; line-height: 10px; color: var(--gold-dark); font-weight: 600;
  }
  .neck-label__script {
    font-family: 'Great Vibes', cursive; font-size: 32px; color: var(--ink-black); margin-top: 2px;
  }

  /* Main label */
  .main-label {
    position: absolute; left: 302px; top: 502px; width: 596px; height: 430px;
    background: var(--navy); border-radius: 14px 14px 0 0; overflow: hidden; text-align: center;
  }
  .main-label__flag {
    position: absolute; left: 284px; top: 42px; width: 28px; height: 20px; background: var(--swiss-red);
  }
  .main-label__brand {
    position: absolute; left: 0; right: 0; top: 70px;
    font-family: 'Cinzel', serif; font-weight: 700; font-size: 42px; color: var(--gold);
  }
  .main-label__distillery {
    position: absolute; left: 0; right: 0; top: 120px;
    font-family: 'Cormorant Garamond', serif; font-weight: 500; font-size: 11px; letter-spacing: 1.5px; color: var(--white);
  }
  .main-label__title {
    position: absolute; left: 0; right: 0; top: 170px;
    font-family: 'Cinzel', serif; font-weight: 700; font-size: 40px; letter-spacing: 2px; color: var(--gold);
  }
  .main-label__subtitle {
    position: absolute; left: 0; right: 0; top: 220px;
    font-family: 'Cinzel', serif; font-weight: 600; font-size: 17px; letter-spacing: 1.5px; color: var(--gold);
  }
  .main-label__script {
    position: absolute; left: 0; right: 0; top: 238px;
    font-family: 'Great Vibes', cursive; font-size: 82px; color: var(--silver);
  }
  .main-label__ridge {
    position: absolute; left: 0; bottom: 0; width: 596px; height: 96px;
    background: linear-gradient(to bottom, var(--navy) 0%, #c9cfd9 70%, var(--white) 100%);
  }

  /* Info panel */
  .info-panel {
    position: absolute; left: 372px; top: 949px; width: 456px; height: 193px;
    background: var(--paper); color: var(--paper-ink);
  }
  .info-panel__story {
    position: absolute; left: 26px; top: 20px; width: 166px;
    font-family: 'Cormorant Garamond', serif; font-style: italic; font-size: 9px; line-height: 14.5px;
  }
  .info-panel__age {
    position: absolute; left: 199px; top: 18px; width: 62px; text-align: center;
    font-family: 'Cinzel', serif; color: var(--gold-dark);
  }
  .age__label { font-size: 14px; border-bottom: 1px solid var(--gold-dark); border-top: 1px solid var(--gold-dark); line-height: 16px; }
  .age__number { font-size: 46px; font-weight: 700; line-height: 44px; color: var(--ink-black); }
  .age__unit { font-size: 14px; line-height: 14px; }
  .info-panel__facts {
    position: absolute; left: 274px; top: 24px; width: 170px;
    font-family: 'Cormorant Garamond', serif; font-style: italic; font-size: 10px;
  }
  .facts__row { height: 23px; border-bottom: 1px solid #cfc6b3; padding-top: 3px; }
  .facts__sig { font-family: 'Great Vibes', cursive; font-style: normal; font-size: 17px; color: var(--ink-black); margin-left: 4px; }
  .info-panel__oak {
    position: absolute; left: 0; right: 0; top: 114px; display: flex; justify-content: center; align-items: center; gap: 6px;
    font-family: 'Cinzel', serif; font-size: 12px; letter-spacing: 0.5px;
  }
  .oak__barrel { width: 30px; height: 26px; border-radius: 6px; background: linear-gradient(#9e9a93, #6e6a63); }
  .info-panel__volume {
    position: absolute; left: 0; right: 0; top: 153px; text-align: center;
    font-family: 'Cinzel', serif; font-size: 10px; letter-spacing: 0.5px;
  }
  .info-panel__producer {
    position: absolute; left: 0; right: 0; top: 173px; text-align: center;
    font-family: 'Cinzel', serif; font-size: 10px; color: var(--gold-dark); letter-spacing: 0.3px;
  }
  .info-panel__seal { position: absolute; left: 398px; top: 94px; width: 82px; height: 82px; }
</style>
</head>
<body>
<main class="canvas">

  <section class="neck-label">
    <div class="neck-label__band"><span class="neck-label__title">Gran Reserva</span></div>
    <div class="neck-label__foot">
      <div class="neck-label__sub">Very Special<br>Pot Still</div>
      <div class="neck-label__script">Brandy</div>
    </div>
  </section>

  <section class="main-label">
    <div class="main-label__flag"></div>
    <div class="main-label__brand">Velostine</div>
    <div class="main-label__distillery">SWISS DISTILLERY</div>
    <h1 class="main-label__title">Gran Reserva</h1>
    <div class="main-label__subtitle">Very Special Pot Still</div>
    <div class="main-label__script">Brandy</div>
    <div class="main-label__ridge" role="img" aria-label="Alpine mountain ridge silhouette"></div>
  </section>

  <section class="info-panel">
    <p class="info-panel__story">This brandy is crafted from carefully selected grapes, distilled in Copper Pot Stills, and aged for at least 6 years in French Oak Barrels. The long aging process allows the Brandy to develop complex flavors and a smooth, rich character.</p>
    <div class="info-panel__age">
      <div class="age__label">Aged</div>
      <div class="age__number">6</div>
      <div class="age__unit">Years</div>
    </div>
    <div class="info-panel__facts">
      <div class="facts__row">Cask No.: 100</div>
      <div class="facts__row">Bottle No.: 100/500</div>
      <div class="facts__row">Brandy Maker: <span class="facts__sig">R. Amsler</span></div>
    </div>
    <div class="info-panel__oak">
      <span>Aged in French</span>
      <span class="oak__barrel" role="img" aria-label="Oak barrels"></span>
      <span>Oak Barrels</span>
    </div>
    <div class="info-panel__volume">45% Alc. Vol. | 750 ML</div>
    <div class="info-panel__producer">Produced by Velostine Swiss Distillery, Switzerland</div>
    <svg class="info-panel__seal" viewBox="0 0 82 82" role="img" aria-label="Wax seal">
      <circle cx="41" cy="41" r="39" fill="var(--wax)"/>
      <circle cx="41" cy="41" r="28" fill="none" stroke="#c8343a" stroke-width="2"/>
    </svg>
  </section>

</main>
</body>
</html>
```